Corporate travel agency website design

Hello I need a website design that will look professional. I want that anyone that gos on our site understands that we are a large successful company. I want it to be up to par with other large companies. The site should be sleek and neat.
Below I will attach my logo. A recent one page add I made and content for my add that will be used for the website.

```html
<!DOCTYPE html>
<html lang="en">
<head>
<meta charset="utf-8">
<title>Aeris Travel – Corporate Travel Management</title>
<link href="https://fonts.googleapis.com/css2?family=Montserrat:wght@400;500;600;700&family=Lato:wght@400;700&display=swap" rel="stylesheet">
<style>
:root{
  --navy:#0d1a33;
  --navy-deep:#091327;
  --navy-mid:#14254a;
  --sky:#cdeaf8;
  --sky-strong:#a9dcf4;
  --ink:#1b1b1b;
  --text:#3a3a3a;
  --line:#8a8f99;
  --white:#ffffff;
}
*{margin:0;padding:0;box-sizing:border-box}
html,body{width:1200px;height:4777px;overflow:hidden}
body{position:relative;background:var(--white);font-family:"Lato",sans-serif;color:var(--text)}
.abs{position:absolute}

/* top bar & nav */
.topbar{left:0;top:0;width:1200px;height:48px;background:var(--sky)}
.topbar-item{top:13px;font-family:"Montserrat",sans-serif;font-size:16px;font-weight:500;color:var(--navy);display:flex;align-items:center;gap:10px}
.nav{left:0;top:48px;width:1200px;height:69px;background:var(--white);box-shadow:0 2px 6px rgba(0,0,0,.08)}
.nav a{position:absolute;top:24px;font-family:"Montserrat",sans-serif;font-size:15px;color:var(--ink);text-decoration:none}
.nav a.active{font-weight:700;border-bottom:2px solid var(--ink)}
.brand-box{left:93px;top:0;width:209px;height:134px;background:var(--navy);box-shadow:0 4px 10px rgba(0,0,0,.3);display:flex;flex-direction:column;align-items:center;justify-content:center;gap:12px;z-index:3}
.brand-name{font-family:"Montserrat",sans-serif;font-weight:600;color:var(--white)}
.brand-square{width:16px;height:16px;background:var(--white)}

/* chevron buttons */
.btn{position:absolute}
.btn .edge,.btn .face{position:absolute;top:0;height:100%;clip-path:polygon(0 0,90% 0,100% 50%,90% 100%,0 100%,8% 50%)}
.btn .edge{left:5px;width:100%;background:var(--sky-strong)}
.btn .face{left:0;width:100%;background:var(--navy);color:var(--white);display:flex;align-items:center;justify-content:center;font-family:"Montserrat",sans-serif;font-weight:700}
.btn.light .face{background:var(--sky);color:var(--navy)}
.btn.light .edge{background:var(--white)}

/* hero */
.hero{left:0;top:117px;width:1200px;height:597px;background:linear-gradient(100deg,#3a2b20 0%,#8a5a2c 30%,#c98a3f 55%,#e9b25a 75%,#f5d27e 100%)}
.hero-card{left:512px;top:267px;width:592px;height:293px;background:rgba(12,24,48,.9);text-align:center;color:var(--white)}
.hero-card h1{margin-top:56px;font-family:"Montserrat",sans-serif;font-size:31px;font-weight:700;letter-spacing:.5px}
.hero-card h2{margin-top:6px;font-family:"Montserrat",sans-serif;font-size:21px;font-weight:500;letter-spacing:.5px}
.hero-card p{margin-top:12px;font-size:15px}

/* shared titles */
.section-title{width:1200px;left:0;text-align:center;font-family:"Montserrat",sans-serif;font-weight:700}
.heading{color:var(--ink)}
.title-mark{width:14px;height:14px;border:2px solid currentColor;left:593px}
.why-text{left:119px;top:878px;width:962px;text-align:center;font-size:15px;line-height:25.6px;color:var(--text)}

/* band */
.band{left:0;top:1169px;width:1200px;height:345px;background:linear-gradient(180deg,#1c2d4f 0%,#14254a 45%,#0d1a33 100%);clip-path:polygon(0 0,100% 0,100% 80%,50% 100%,0 80%)}
.band-box{left:529px;top:1187px;width:141px;height:134px;background:var(--navy-deep)}
.band-name{top:1322px;color:var(--white);font-size:26px;font-weight:400}
.band-tag{top:1360px;color:var(--white);font-size:23px;font-weight:700}

/* wheel */
.octagon{left:386px;top:1679px;width:390px;height:390px;background:var(--navy-deep);clip-path:polygon(29% 0,71% 0,100% 29%,100% 71%,71% 100%,29% 100%,0 71%,0 29%);display:flex;flex-direction:column;align-items:center;justify-content:center;gap:16px}
.feature{width:114px;height:114px;border-radius:50%;border:3px solid var(--navy);background:var(--white);transform:translate(-50%,-50%)}
.feature::after{content:"";position:absolute;left:50%;top:50%;width:44px;height:44px;transform:translate(-50%,-50%);border:2px solid var(--navy);border-radius:6px}
.feature-label{transform:translateX(-50%);text-align:center;font-family:"Montserrat",sans-serif;font-size:16px;font-weight:600;color:var(--ink);line-height:25px;white-space:nowrap}

/* services */
.services{left:0;top:2295px;width:1200px;height:1440px;background:linear-gradient(160deg,#13244a 0%,#0d1a33 40%,#0b1730 70%,#132a52 100%)}
.photo{position:absolute}
.frame{position:absolute;border:3px solid #c8d3e6}
.svc-title{font-family:"Montserrat",sans-serif;font-weight:700;font-size:27px;color:var(--white)}
.svc-text{font-size:14.5px;line-height:25.7px;color:#d7deeb}

/* contact */
.contact-text{left:150px;top:3866px;width:900px;text-align:center;font-size:14.5px;line-height:25.6px}
.field-label{font-size:14.5px;color:var(--ink)}
.field-line{height:2px;background:var(--line)}

/* footer */
.footer{left:0;top:4291px;width:1200px;height:486px;background:var(--navy)}
.foot-link{position:absolute;top:4509px;transform:translateX(-50%);color:var(--white);font-family:"Montserrat",sans-serif;font-size:16px;text-decoration:none;white-space:nowrap}
.f-icon{width:52px;height:52px;background:var(--sky);display:flex;align-items:center;justify-content:center}
.f-text{top:4580px;color:var(--white);font-family:"Montserrat",sans-serif;font-size:16px}
</style>
</head>
<body>

<!-- top bar -->
<div class="abs topbar"></div>
<div class="abs topbar-item" style="left:575px">
  <svg width="20" height="20" viewBox="0 0 24 24"><rect width="24" height="24" rx="4" fill="#0d1a33"/><path d="M8 5l2.5 3-1.5 2c1 2 2.5 3.5 4.5 4.5l2-1.5 3 2.5-1.5 2.5C12 18 6 12 5.5 6.5z" fill="#cdeaf8"/></svg>
  Call : +1 800 555 0142
</div>
<div class="abs topbar-item" style="left:857px">
  <svg width="20" height="20" viewBox="0 0 24 24"><rect width="24" height="24" rx="4" fill="#0d1a33"/><path d="M5 7h14v10H5z" fill="#cdeaf8"/><path d="M5 7l7 6 7-6" stroke="#0d1a33" stroke-width="1.6" fill="none"/></svg>
  Mail : hello@aeristravel.example
</div>

<!-- navigation -->
<nav class="abs nav">
  <a class="active" href="#" style="left:505px">Home</a>
  <a href="#" style="left:617px">Services</a>
  <a href="#" style="left:738px">Why Choose Aeris Travel?</a>
</nav>
<div class="btn" style="left:946px;top:57px;width:150px;height:52px">
  <span class="edge"></span><span class="face" style="font-size:17px;clip-path:polygon(0 0,90% 0,100% 50%,90% 100%,0 100%)">Contact Us</span>
</div>
<div class="abs brand-box">
  <span class="brand-square"></span>
  <span class="brand-name" style="font-size:18px">Aeris Travel</span>
</div>

<!-- hero -->
<div class="abs hero" role="img" aria-label="Traveller walking with a suitcase through a sunlit airport terminal"></div>
<div class="abs hero-card">
  <h1>WELCOME TO AERIS TRAVEL</h1>
  <h2>BUSINESS TRAVEL REINVENTED</h2>
  <p>Aeris Travel,We're your corporate travel partner to help you manage it all.</p>
</div>
<div class="btn light" style="left:714px;top:447px;width:184px;height:50px">
  <span class="edge"></span><span class="face" style="font-size:18px">Get Started</span>
</div>

<!-- why choose -->
<span class="abs title-mark" style="top:792px;color:var(--navy)"></span>
<h2 class="abs section-title heading" style="top:826px;font-size:32px">Why Choose Aeris Travel?</h2>
<p class="abs why-text">Aeris Travel is a global leader in business travel management services. We drive savings, efficiency, and unparalleled service to businesses and their travelers all around the world. If you are looking for a tailored travel managed solution focused on offering white glove service and fulfilling your individual preferences ,while delivering customer excellence, you've come to the right place. At Aeris Travel, our mission is to have you focus on your day to day business while we handle all of the logistics and details for the most successful all encompassing travel experience. From emergency passport arrangements to last minute cancellations, re-bookings, and other intricate travel challenges, Aeris Travel is well versed in handling the routine array of travel services, as well as solving any travel related issue that might arise.</p>
<div class="btn" style="left:506px;top:1052px;width:184px;height:50px">
  <span class="edge"></span><span class="face" style="font-size:18px">Read More</span>
</div>

<!-- partner band -->
<div class="abs band" role="img" aria-label="Dusky city skyline in deep navy tones"></div>
<div class="abs band-box"></div>
<div class="abs section-title band-name">Aeris Travel</div>
<div class="abs section-title band-tag">Aeris Travel,We're your corporate travel partner to help you manage it all.</div>
<svg class="abs" style="left:596px;top:1398px" width="48" height="48" viewBox="0 0 48 48"><path d="M44 6C24 6 12 16 8 40" stroke="#fff" stroke-width="2.5" fill="none"/><path d="M2 30l6 11 9-8" stroke="#fff" stroke-width="2.5" fill="none"/></svg>

<!-- feature wheel -->
<div class="abs octagon">
  <span class="brand-square" style="width:20px;height:20px"></span>
  <span class="brand-name" style="font-size:28px">Aeris Travel</span>
</div>

<div class="abs feature" style="left:486px;top:1627px" role="img" aria-label="Budget report icon"></div>
<div class="abs feature" style="left:673px;top:1627px" role="img" aria-label="Car and hotel service icon"></div>
<div class="abs feature" style="left:341px;top:1777px" role="img" aria-label="Speed gauge icon"></div>
<div class="abs feature" style="left:827px;top:1784px" role="img" aria-label="Savings coins icon"></div>
<div class="abs feature" style="left:339px;top:1964px" role="img" aria-label="Gloved hand icon"></div>
<div class="abs feature" style="left:820px;top:1977px" role="img" aria-label="Clipboard checklist icon"></div>
<div class="abs feature" style="left:490px;top:2115px" role="img" aria-label="Policy document icon"></div>
<div class="abs feature" style="left:677px;top:2113px" role="img" aria-label="Expense workflow icon"></div>

<div class="abs feature-label" style="left:495px;top:1517px">Budget and Travel<br>Spend Reporting</div>
<div class="abs feature-label" style="left:686px;top:1533px">Unparalled Service</div>
<div class="abs feature-label" style="left:336px;top:1849px">Efficiency</div>
<div class="abs feature-label" style="left:864px;top:1849px">Unparallel Savings</div>
<div class="abs feature-label" style="left:341px;top:2038px">White Glove Service</div>
<div class="abs feature-label" style="left:827px;top:2036px">Full Service travel<br>management program</div>
<div class="abs feature-label" style="left:484px;top:2177px">Aeris travel policy<br>compliance</div>
<div class="abs feature-label" style="left:679px;top:2177px">Streamlined expense<br>reports</div>

<!-- travel management service -->
<div class="abs services" role="img" aria-label="Dark navy background with subtle geometric texture"></div>
<span class="abs title-mark" style="top:2356px;color:#c8d3e6"></span>
<h2 class="abs section-title" style="top:2400px;font-size:31px;color:var(--white)">Travel Management Service</h2>

<div class="frame" style="left:111px;top:2480px;width:440px;height:341px;border-left:none;border-top:none"></div>
<div class="photo" style="left:98px;top:2467px;width:434px;height:332px;background:linear-gradient(135deg,#b07a63 0%,#8d6a55 35%,#5f7a3a 60%,#3f5a2a 100%)" role="img" aria-label="Landscaper laying fresh turf beside a paved path"></div>
<h3 class="abs svc-title" style="left:607px;top:2540px">Unparalled Service</h3>
<p class="abs svc-text" style="left:607px;top:2583px;width:470px">Aeris Travel is famous for our concierge style approach to travel. From detailed planning, to commercial or private air travel, transportation, including car rentals, chauffers, busses for larger groups, hotels, all styles of lodging accomodations, special event planning and more, Aeris Travel is like having your own personal or corporate travel butler.</p>

<h3 class="abs svc-title" style="left:95px;top:2868px">Budget and Travel Spend Reporting</h3>
<p class="abs svc-text" style="left:100px;top:2910px;width:466px">Having a travel management service will ensure that your company enforces corporate compliance and maintains control over travel decisions. This ensures that your employees stick to your budget, which in turn will protect your bottom line. Travel expenses can be costly. Having a savvy and experienced corporate travel manager who can access deep discounts not available to the public will ensure your travel is booked across the board at the lowest prices expenses are kept under control. Travel reporting is critical to optimizing budgets, streamlining expense reports, and recognizing key trends. Aeris-Travel customizes travel spend reports, by team, project, department etc, so companies can accurately track travel expenses, and make critical decisions based on the spend.</p>
<div class="frame" style="left:647px;top:2907px;width:440px;height:336px;border-right:none;border-top:none"></div>
<div class="photo" style="left:664px;top:2888px;width:436px;height:332px;background:linear-gradient(120deg,#6e7a86 0%,#3b4450 40%,#1d232d 70%,#6a5344 100%)" role="img" aria-label="Businessman working on a laptop and tablet aboard a train"></div>

<div class="frame" style="left:111px;top:3329px;width:440px;height:333px;border-left:none"></div>
<div class="photo" style="left:98px;top:3309px;width:434px;height:331px;background:linear-gradient(110deg,#2f3a3f 0%,#5f6d6b 35%,#9aa4a0 60%,#c7cdd0 100%)" role="img" aria-label="Hand holding a phone beside an efficiency rating chart and keyboard"></div>
<h3 class="abs svc-title" style="left:607px;top:3328px">Efficiency</h3>
<p class="abs svc-text" style="left:607px;top:3371px;width:470px">Time is your most valuable tool! Our goal at Aeris Travel is to have your employees' complete focus be on your core business, while having us handle all the logistics for their travel. One of the most appreciated services we offer is the management of travel headaches. Unforeseen circumstances such as cancellations, missed flights, cancelled flights, last minute bookings or changed plans, can take hours to rectify. Aeris Travel handles all of these tedious repositionings expeditiously, saving your employees precious time. Give your company a competitive edge by having Aeris Travel handle your team's travel arrangements.</p>

<!-- contact -->
<span class="abs title-mark" style="top:3782px;color:var(--navy)"></span>
<h2 class="abs section-title heading" style="top:3820px;font-size:32px">Contact Us</h2>
<p class="abs contact-text">Aeris Travel is a global leader in business travel management services. We drive savings, efficiency, and unparalleled service to businesses and their travelers all around the world.</p>

<form>
  <label class="abs field-label" style="left:202px;top:3956px">Enter Name :</label>
  <div class="abs field-line" style="left:202px;top:3985px;width:371px"></div>
  <label class="abs field-label" style="left:612px;top:3956px">Last Name :</label>
  <div class="abs field-line" style="left:612px;top:3985px;width:371px"></div>
  <label class="abs field-label" style="left:202px;top:4022px">Email Address :</label>
  <div class="abs field-line" style="left:202px;top:4053px;width:371px"></div>
  <label class="abs field-label" style="left:612px;top:4022px">Phone Number :</label>
  <div class="abs field-line" style="left:612px;top:4053px;width:371px"></div>
  <label class="abs field-label" style="left:202px;top:4077px">Message :</label>
  <div class="abs field-line" style="left:204px;top:4140px;width:794px"></div>
</form>
<div class="btn" style="left:506px;top:4192px;width:184px;height:51px">
  <span class="edge"></span><span class="face" style="font-size:18px">Read More</span>
</div>

<!-- footer -->
<footer class="abs footer"></footer>
<span class="abs brand-square" style="left:589px;top:4390px;width:22px;height:22px;background:var(--sky)"></span>
<div class="abs section-title brand-name" style="top:4428px;font-size:19px;font-weight:600">Aeris Travel</div>

<a class="foot-link" href="#" style="left:371px">Home</a>
<a class="foot-link" href="#" style="left:466px">Services</a>
<a class="foot-link" href="#" style="left:631px">Why Choose Aeris Travel?</a>
<a class="foot-link" href="#" style="left:809px">Contact Us</a>

<div class="abs f-icon" style="left:152px;top:4567px">
  <svg width="26" height="20" viewBox="0 0 26 20"><rect width="26" height="20" rx="2" fill="#0d1a33"/><path d="M1 2l12 9 12-9" stroke="#cdeaf8" stroke-width="2" fill="none"/></svg>
</div>
<span class="abs f-text" style="left:226px">www.aeristravel.example</span>
<div class="abs f-icon" style="left:504px;top:4567px">
  <svg width="20" height="28" viewBox="0 0 20 28"><path d="M10 0C4.5 0 0 4.5 0 10c0 7 10 18 10 18s10-11 10-18C20 4.5 15.5 0 10 0z" fill="#0d1a33"/><circle cx="10" cy="10" r="4" fill="#cdeaf8"/></svg>
</div>
<span class="abs f-text" style="left:575px">Aeris Travel,United State.</span>
<div class="abs f-icon" style="left:861px;top:4567px">
  <svg width="24" height="24" viewBox="0 0 24 24"><path d="M5 2l4 5-2.5 3c1.5 3 4 5.5 7.5 7.5l3-2.5 5 4-2.5 4C10 22 2 14 1.5 4.5z" fill="#0d1a33"/></svg>
</div>
<span class="abs f-text" style="left:933px">+1 800 555 0142</span>

<div class="abs" style="left:98px;top:4712px;width:1006px;height:1px;background:#8693ad"></div>
<div class="abs section-title" style="top:4734px;font-size:15px;font-weight:500;color:var(--white)">Copyrights@2023.AERIS TRAVEL.All Rights Reserved</div>

</body>
</html>
```